Flyer design to fit banner mock-up

Create a one-page flyer in an adobe program (InDesign, Photoshop, Acrobat). The flyer should be created for high-quality print, 300 dpi, full bleed. Use the provided text (see attached word doc) and logo (see attached eps file). The style of the flyer should be similar to our display banner (see attached image of banner mock-up). Deliverables should include a print-quality PDF and all adobe design files.

Industry/Entity Type

Technology Equipment

Font styles to use
Sans Serif

Colors

Designer to choose colors to be used in the design.

Requirements
Must have
• Logo; text provided in word document.

```html
<!DOCTYPE html>
<html lang="en">
<head>
<meta charset="utf-8">
<title>4 Hidden Costs in Your Firewall – Veltrix Security</title>
<link rel="stylesheet" href="https://fonts.googleapis.com/css2?family=Open+Sans:wght@400;600;700&family=Roboto+Condensed:wght@700&display=swap">
<style>
  :root {
    --backdrop: #e6e4e3;
    --paper: #f4f4f5;
    --band: #f2dcd6;
    --band-soft: #f7e9e5;
    --red: #d4534e;
    --yellow: #e6ad52;
    --ink: #48484c;
    --text: #5c5c60;
    --muted: #7a7a7e;
  }
  * { box-sizing: border-box; margin: 0; padding: 0; }
  html, body { width: 1200px; height: 854px; overflow: hidden; }
  body {
    background: var(--backdrop);
    font-family: "Open Sans", Arial, sans-serif;
    color: var(--text);
    position: relative;
  }
  .flyer {
    position: absolute;
    left: 300px; top: 27px;
    width: 600px; height: 800px;
    background: var(--paper);
    overflow: hidden;
    box-shadow: 0 6px 24px rgba(0,0,0,.12);
  }
  .flyer-band { position: absolute; inset: 0; }
  .brand {
    position: absolute; left: 38px; top: 72px;
    display: flex; align-items: center; gap: 8px;
    font-weight: 700; font-size: 20px; color: var(--red);
    letter-spacing: .5px;
  }
  .brand-dot { width: 10px; height: 10px; border-radius: 50%; background: var(--red); }
  .product-visual {
    position: absolute; left: 262px; top: 26px;
    width: 170px; height: 150px; border-radius: 50%;
    background: radial-gradient(circle, #4a4a4f 0 45%, #8a8a8f 46% 58%, var(--red) 59% 66%, transparent 67%);
  }
  .headline {
    position: absolute; left: 38px; top: 192px;
    font-family: "Roboto Condensed", "Arial Narrow", sans-serif;
    font-weight: 700; font-size: 44px; line-height: 42px;
    text-transform: uppercase; color: var(--ink);
  }
  .headline .accent { color: var(--red); }
  .costs { position: absolute; left: 38px; top: 336px; width: 524px; }
  .cost { margin-bottom: 13px; }
  .cost:last-child { margin-bottom: 0; }
  .cost h2 {
    font-family: "Roboto Condensed", "Arial Narrow", sans-serif;
    font-weight: 700; font-size: 14px; color: var(--red);
    margin-bottom: 3px;
  }
  .cost p { font-size: 9px; line-height: 13px; }
  .cost .quote { font-style: italic; color: var(--muted); margin-top: 2px; }
  .cta {
    position: absolute; left: 0; right: 0; top: 686px; text-align: center;
    font-family: "Roboto Condensed", "Arial Narrow", sans-serif;
    font-weight: 700; font-size: 20px; color: var(--red);
  }
  .legal {
    position: absolute; left: 0; right: 0; top: 716px; text-align: center;
    font-size: 8px; color: var(--muted);
  }
  .footer-swoosh { position: absolute; left: 0; bottom: 0; }
  .contact {
    position: absolute; right: 34px; bottom: 22px;
    display: flex; gap: 20px; font-size: 9px; color: var(--ink);
  }
  .contact-item { display: flex; align-items: center; gap: 6px; }
  .contact-icon {
    width: 16px; height: 16px; display: flex; align-items: center; justify-content: center;
  }
  .contact-icon.phone { background: var(--ink); }
  .contact-icon.web { background: var(--yellow); }
</style>
</head>
<body>
  <main class="flyer">
    <svg class="flyer-band" width="600" height="800" viewBox="0 0 600 800" aria-hidden="true">
      <polygon points="90,0 330,0 600,330 600,520 120,520 0,390 0,150" fill="var(--band-soft)"/>
      <polygon points="150,0 330,0 420,520 120,520 0,390 0,260" fill="var(--band)"/>
    </svg>

    <div class="brand"><span class="brand-dot"></span>Veltrix Security</div>

    <div class="product-visual" role="img" aria-label="Stack of rack-mounted firewall appliances inside a red dashed ring"></div>

    <h1 class="headline">
      <span>4 Hidden</span><br>
      <span class="accent">Costs in Your</span><br>
      <span>Firewall</span>
    </h1>

    <section class="costs">
      <article class="cost">
        <h2>1. Tech Support</h2>
        <p>When you need help, you need a fast, responsive partner who will solve your problem. Unfortunately, most firewall vendors offer hassle-filled tech support, which can cost you hours of lost time a year.</p>
        <p class="quote">“Every time I've called Veltrix tech support, they knew exactly what I was talking about and I got my question answered within minutes.” Lena Hart, Owner, Hart IT</p>
      </article>
      <article class="cost">
        <h2>2. Ease of Use</h2>
        <p>A complicated firewall takes more time to set up and manage. This robs you of hours, and the cost racks up by the hour.</p>
        <p class="quote">“GateKeeper One is much easier to use than the other firewalls on the market. There's no compromise in the quality of the hardware or the security.” Omar Reyes, CEO, Northfield Computing</p>
      </article>
      <article class="cost">
        <h2>3. Partner Programs</h2>
        <p>The way you pay for a firewall can greatly impact your profit. For example, if your clients pay monthly and you pay by the year, then you take on a lot of risk, and sometimes risk hurts.</p>
        <p class="quote">“I offer a maintenance/security package bundled with GateKeeper One and it's my bread and butter. My customers pay monthly and I don't have to sell them a new license every year. You can't go wrong with it.” Paul Whitfield, Owner, Whitfield Computer Services</p>
      </article>
      <article class="cost">
        <h2>4. Security Features</h2>
        <p>A firewall with outdated security may be cheap upfront, but it will cost you down the road. Outdated security does not protect your clients. That means more malware and data breaches, and that means more hours spent solving problems.</p>
        <p class="quote">“Veltrix is part of the core solution that we provide to our clients and I'm certain that partnering with them has made my business more efficient and my clients safer.” Grace Moreno, CEO, Summit Network Support</p>
      </article>
    </section>

    <p class="cta">Want to know more? Visit veltrixsecure.com</p>
    <p class="legal">© 2020 Veltrix Security Corp | All Rights Reserved | www.veltrixsecure.com | 800.555.0142</p>

    <svg class="footer-swoosh" width="600" height="120" viewBox="0 0 600 120" aria-hidden="true">
      <path d="M0,20 C60,20 110,40 150,120 L0,120 Z" fill="var(--red)"/>
      <path d="M0,42 C55,42 95,62 125,120 L0,120 Z" fill="var(--yellow)"/>
      <path d="M0,64 C45,64 78,82 100,120 L0,120 Z" fill="var(--ink)"/>
    </svg>

    <div class="contact">
      <span class="contact-item">
        <span class="contact-icon phone">
          <svg width="10" height="10" viewBox="0 0 24 24" aria-hidden="true"><path fill="#fff" d="M6.6 10.8a15 15 0 0 0 6.6 6.6l2.2-2.2a1 1 0 0 1 1-.25 11.4 11.4 0 0 0 3.6.57 1 1 0 0 1 1 1V20a1 1 0 0 1-1 1A17 17 0 0 1 3 4a1 1 0 0 1 1-1h3.5a1 1 0 0 1 1 1c0 1.250.2 2.450.57 3.57a1 1 0 0 1-.25 1z"/></svg>
        </span>800.555.0142
      </span>
      <span class="contact-item">
        <span class="contact-icon web">
          <svg width="10" height="10" viewBox="0 0 24 24" aria-hidden="true"><circle cx="12" cy="12" r="9" fill="none" stroke="#fff" stroke-width="2"/><path d="M3 12h18M12 3c3 3 3 15 0 18M12 3c-3 3-3 15 0 18" fill="none" stroke="#fff" stroke-width="1.6"/></svg>
        </span>www.veltrixsecure.com
      </span>
    </div>
  </main>
</body>
</html>
```